Valdane Companies Business Card Design

We need a new business card for our Private Equity Real Estate Development firm, “Valdane” and our EB-5 regional center “Thornmere Regional Center” on one card. We prefer a design that is simple, elegant, and represents the luxury products we design and build as well as the financial security and stability our successful history has produced. We are an industry leader in our field and 3rd generation family business that has evolved into an institutional quality investment platform. Considered design size is standard business card dimensions (3.5 x 2 inches with an additional 1/8 inch space for design elements or backgrounds that extend beyond the finished size of your piece.

Target Market(s)

• High net worth individuals
• Highly skilled technical workers and physicians in the US seeking investment-based immigration opportunities
• Sophisticated private equity investors
• Intermediary partners include domestic attorneys and investment brokers, as well as international agent networks
• US real estate developers

Industry/Entity Type

Finance

Contact Information for Business Card

(Providing placeholder info for personal information, please design for longer character spaces, longer names and addresses etc..)
• Logo for Valdane
• Logo for Thornmere Regional Center
• Full name: Marcus Valdane
• Job title: CEO
• Email address: mvaldane@valdanecompanies.com
• Cell phone number: +1.555.314.2287
• Office number +1.555.628.4410
• Office address: Larkfield Court 5, 4817 Vista Orilla, Brightwater, CA.
• Website: www.valdanecompanies.com

Font styles to use
Serif
Sans Serif

Colors
ec1f27
ffffff
000000

Requirements
Must have
• • Logo for Valdane
• • Logo for Thornmere Regional Center
• - Use rounded corners
• (See .ai file included for logos)
Nice to have
• • Simple, elegant design
• • Aesthetically compatible with our website design (www.valdanecompanies.com)
• • Color palette including but not limited to white, black, and red (as per logos)
Should not have
• - Not too much red color
• - Do not stack both logos on top of each other

```html
<!DOCTYPE html>
<html lang="en">
<head>
<meta charset="utf-8">
<title>Valdane Companies Business Card</title>
<link href="https://fonts.googleapis.com/css2?family=Cinzel:wght@700&family=Roboto:wght@400;700&display=swap" rel="stylesheet">
<style>
  :root {
    --red: #b5172e;
    --black: #111111;
    --grey: #4a4a4a;
    --card: #f7f7f7;
    --ground: #2b2b2b;
    --charcoal: #3a3a3a;
  }
  * { box-sizing: border-box; margin: 0; padding: 0; }
  html, body { width: 1200px; height: 886px; overflow: hidden; }
  body { background: var(--ground); position: relative; font-family: "Roboto", Arial, sans-serif; }

  .card {
    position: absolute;
    width: 580px; height: 331px;
    background: var(--card);
    border-radius: 22px;
  }

  /* Back side */
  .card-back { left: 70px; top: 110px; }
  .back-brand {
    position: absolute; left: 0; right: 0; top: 124px;
    display: flex; align-items: center; justify-content: center; gap: 16px;
  }
  .brand-mark { width: 30px; height: 30px; background: var(--charcoal); flex: none; }
  .brand-name {
    font-family: "Cinzel", Georgia, serif; font-weight: 700;
    font-size: 34px; letter-spacing: 2px; color: var(--charcoal); line-height: 1;
  }
  .back-web {
    position: absolute; left: 0; right: 0; bottom: 44px; text-align: center;
    font-size: 14px; letter-spacing: 3px; color: var(--grey);
  }

  /* Front side */
  .card-front { left: 560px; top: 480px; }
  .center-name {
    position: absolute; left: 40px; top: 30px;
    font-family: "Cinzel", Georgia, serif; font-weight: 700; color: var(--red);
    line-height: 1;
  }
  .center-name .main { display: block; font-size: 30px; letter-spacing: 1px; }
  .center-name .sub { display: block; font-size: 11px; letter-spacing: 5.6px; margin-top: 4px; }
  .person { position: absolute; left: 40px; top: 100px; }
  .person-name { font-size: 20px; font-weight: 700; color: var(--red); letter-spacing: .5px; }
  .person-title { font-size: 13px; color: var(--black); margin-top: 2px; }
  .address {
    position: absolute; left: 40px; top: 160px;
    font-size: 13px; line-height: 17px; color: var(--grey); font-style: normal;
  }
  .contacts { position: absolute; left: 40px; top: 222px; list-style: none; font-size: 13px; line-height: 18px; color: var(--grey); }
  .contacts li { display: flex; align-items: center; gap: 8px; }
  .contacts svg { width: 12px; height: 12px; fill: var(--red); flex: none; }
</style>
</head>
<body>

<section class="card card-back" aria-label="Card back">
  <div class="back-brand">
    <span class="brand-mark"></span>
    <span class="brand-name">VALDANE CAPITAL</span>
  </div>
  <p class="back-web">www.valdanecompanies.com</p>
</section>

<section class="card card-front" aria-label="Card front">
  <h1 class="center-name">
    <span class="main">THORNMERE</span>
    <span class="sub">REGIONAL CENTER</span>
  </h1>
  <div class="person">
    <p class="person-name">MARCUS VALDANE</p>
    <p class="person-title">CEO</p>
  </div>
  <address class="address">
    Larkfield Court 5<br>4817 Vista Orilla<br>Brightwater, CA.
  </address>
  <ul class="contacts">
    <li><svg viewBox="0 0 12 12"><path d="M2.5 0.5l2 2.5-1.2 1.3c.7 1.5 1.9 2.7 3.4 3.4L8 6.5l2.5 2-1.2 2.5C4.8 11 1 7.2 0.5 2.7z"/></svg>+1.555.628.4410</li>
    <li><svg viewBox="0 0 12 12"><path d="M3 0h6a1 1 0 0 1 1 1v10a1 1 0 0 1-1 1H3a1 1 0 0 1-1-1V1a1 1 0 0 1 1-1zm.5 1.5v7.5h5V1.5z"/></svg>+1.555.314.2287</li>
    <li><svg viewBox="0 0 12 12"><path d="M0 2h12v8H0zm1 1v.4l5 3.3 5-3.3V3z"/></svg>mvaldane@valdanecompanies.com</li>
    <li><svg viewBox="0 0 12 12"><circle cx="6" cy="6" r="5.5"/></svg>www.valdanecompanies.com</li>
  </ul>
</section>

</body>
</html>
```